Billboard design 8x3M RAVU (Spanish company)

We´re located in the south of Spain. We run a local telecom company.
We sell Fiber optic, and mobile phone lines mainly.
The billboard will have to be in Spanish, I would like the price to be something you spot on first sight when passing by in the car.
Our company color is blue, like in our logo which I will add. I will also add a example from what we currently have.
The new offer should be:
1000 megas + 100Gigas movil con llamadas ilimitadas. (meaning 1000Mb fiber optic speed and 100Gb data and unlimited calls for 1 mobile line)
Our details are: phone line 958 47 6620
Website: ra-vu.es

```html
<!DOCTYPE html>
<html lang="es">
<head>
<meta charset="utf-8">
<title>RAVU – Valla 8x3</title>
<link href="https://fonts.googleapis.com/css2?family=Oswald:wght@700&family=Saira+Semi+Condensed:wght@600;700&display=swap" rel="stylesheet">
<style>
  :root{
    --navy:#0b4676;
    --cyan:#13b6ec;
    --sun:#fbd452;
    --paper:#ffffff;
    --stage:#e9edf1;
  }
  html,body{margin:0;padding:0;overflow:hidden;}
  body{width:1200px;height:874px;background:var(--stage);position:relative;}
  .billboard{
    position:absolute;left:20px;top:231px;width:1160px;height:412px;
    background:var(--paper);overflow:hidden;
    box-shadow:0 10px 30px rgba(0,0,0,.18);
  }
  .billboard__photo{
    position:absolute;left:630px;top:20px;width:530px;height:360px;
    background:linear-gradient(90deg,#f6f6f4 0%,#f1d36a 28%,#f4f2ee 55%,#e9a98f 78%,#f5f5f3 100%);
    opacity:.85;
  }
  .billboard__art{position:absolute;inset:0;}
  .price{
    position:absolute;left:130px;top:20px;width:300px;text-align:center;
    font-family:"Oswald",sans-serif;font-weight:700;font-size:94px;line-height:1;
    color:var(--navy);letter-spacing:-2px;
  }
  .brand{position:absolute;left:483px;top:14px;width:240px;text-align:center;}
  .brand__name{
    font-family:"Saira Semi Condensed",sans-serif;font-weight:700;font-size:72px;
    line-height:1;color:var(--cyan);letter-spacing:4px;
  }
  .brand__tagline{
    margin-top:4px;font-family:"Saira Semi Condensed",sans-serif;font-weight:600;
    font-size:20px;color:var(--cyan);
  }
  .brand__tagline .strong{color:var(--navy);}
  .offer{
    position:absolute;left:36px;top:204px;width:590px;white-space:nowrap;
    font-family:"Saira Semi Condensed",sans-serif;font-weight:700;font-size:36px;line-height:38px;
  }
  .offer__main{color:var(--navy);margin-left:4px;}
  .offer__extra{color:var(--cyan);}
  .contact{
    position:absolute;left:0;top:340px;height:70px;display:flex;align-items:center;
    font-family:"Saira Semi Condensed",sans-serif;font-weight:600;color:var(--paper);
    white-space:nowrap;
  }
  .contact__icon{width:40px;height:40px;flex:none;}
  .contact__phone{font-size:50px;margin:0 10px 0 8px;letter-spacing:1px;}
  .contact__web{font-size:48px;margin-left:10px;}
  .contact .first{margin-left:28px;}
</style>
</head>
<body>
<div class="billboard">
  <div class="billboard__photo" role="img" aria-label="Fotografía de dos jóvenes sonrientes mirando sus móviles"></div>

  <svg class="billboard__art" width="1160" height="412" viewBox="0 0 1160 412">
    <circle cx="280" cy="42" r="153" fill="var(--sun)"/>
    <circle cx="280" cy="42" r="162" fill="none" stroke="var(--cyan)" stroke-width="2.5" stroke-dasharray="8 6"/>
    <path d="M0 326 L680 318 C740 316 760 368 820 371 L1160 366 L1160 412 L0 412 Z" fill="var(--sun)"/>
    <path d="M0 332 L682 325 C742 323 762 374 822 377 L1160 374 L1160 412 L0 412 Z" fill="var(--navy)"/>
  </svg>

  <div class="price">24,90€</div>

  <div class="brand">
    <div class="brand__name">RAVU</div>
    <div class="brand__tagline">Wifi | Fibra | <span class="strong">Movil | Tv</span></div>
  </div>

  <div class="offer">
    <div class="offer__main">FIBRA OPTICA 1000 MEGAS</div>
    <div class="offer__extra">+ 100 GIGAS MOVIL</div>
    <div class="offer__extra">+ LLAMADAS ILIMITADAS</div>
  </div>

  <div class="contact">
    <svg class="contact__icon first" viewBox="0 0 40 40" aria-hidden="true">
      <circle cx="20" cy="20" r="20" fill="var(--cyan)"/>
      <path d="M14 10c1-1 2.5-1 3 .5l1.5 4c.4 1-.2 1.8-1 2.3l-1 .7c1 2.5 3 4.5 5.5 5.5l.7-1c.5-.8 1.3-1.4 2.3-1l4 1.5c1.5.5 1.5 2 .5 3l-2 2c-1.5 1.5-4 1.5-7-.5-3.5-2.3-6.5-5.3-8.5-8.8-1.800-3-2-5.2-.5-6.7z" fill="var(--paper)"/>
    </svg>
    <span class="contact__phone">958 47 6620</span>
    <svg class="contact__icon" viewBox="0 0 40 40" aria-hidden="true">
      <circle cx="20" cy="20" r="20" fill="var(--cyan)"/>
      <rect x="12" y="12" width="16" height="11" rx="1.5" fill="none" stroke="var(--paper)" stroke-width="2.2"/>
      <rect x="9" y="25" width="22" height="3" rx="1" fill="var(--paper)"/>
    </svg>
    <span class="contact__web">ra-vu.es</span>
  </div>
</div>
</body>
</html>
```